Business card design for Automotive workshop

We need a business card for a new automotive repair and tyre shop called Keelstone Prime Automotive located in New Zealand. We are a clean, modern and fresh workshop and company.

Front needs to feature logo,
my name:
Marlo Fenwicke (director)

Address:
48 Tarn Lane
Harrowby 3682

Phone: 07 594 2713
Mobile: 027 451 9362
Email: office@keelstoneautomotive.example.nz
Website: keelstoneautomotive.example.nz

Back needs to feature an area to write down appointment details, date and time.

Also feature a list of jobs and work we do such as,
Vehicle Servicing
All Mechanical Repairs
Warrant of Fitness
Tyres & Wheel Alignments
Automotive Diagnostics
Automotive Parts & Supplies

```html
<!DOCTYPE html>
<html lang="en">
<head>
<meta charset="utf-8">
<title>Keelstone Prime Automotive – Business Card</title>
<link href="https://fonts.googleapis.com/css2?family=Roboto:wght@400;700&display=swap" rel="stylesheet">
<style>
  :root {
    --red: #e3201f;
    --navy: #2f3a58;
    --navy-dark: #28324c;
    --white: #ffffff;
    --black: #0c0c0c;
    --stage-light: #5a5a5a;
    --stage-dark: #1f1f1f;
  }
  * { margin: 0; padding: 0; box-sizing: border-box; }
  html, body { width: 1200px; height: 750px; overflow: hidden; }
  body {
    position: relative;
    font-family: "Roboto", Arial, sans-serif;
    background: radial-gradient(ellipse 60% 55% at 50% 32%, var(--stage-light), var(--stage-dark));
  }
  .card {
    position: absolute;
    top: 186px;
    width: 560px;
    height: 328px;
    border-radius: 24px;
    background: linear-gradient(160deg, var(--navy), var(--navy-dark));
    box-shadow: 0 4px 10px rgba(0,0,0,.55);
    overflow: hidden;
  }
  .card--front { left: 38px; }
  .card--back { left: 612px; }

  .wordmark {
    position: absolute;
    color: var(--red);
    font-weight: 700;
    font-size: 17px;
    line-height: 19px;
    letter-spacing: 1.5px;
    text-transform: uppercase;
    text-align: center;
    width: 210px;
  }
  .card--front .wordmark { left: 306px; top: 148px; }
  .card--back .wordmark { left: 306px; top: 136px; }

  /* front */
  .name-tab {
    position: absolute; left: 0; top: 70px;
    width: 46px; height: 30px; background: var(--red);
  }
  .icon {
    position: absolute;
    border-radius: 50%;
    background: var(--black);
    display: flex; align-items: center; justify-content: center;
  }
  .icon svg { fill: var(--white); }
  .name-icon { left: 20px; top: 71px; width: 27px; height: 27px; border: 2px solid var(--white); }
  .name {
    position: absolute; left: 52px; top: 71px;
    color: var(--red); font-weight: 700; font-size: 22px; letter-spacing: .6px; word-spacing: 3px;
  }
  .role {
    position: absolute; left: 45px; top: 99px;
    color: var(--red); font-size: 18px; word-spacing: 3px;
  }
  .name-rule {
    position: absolute; left: 40px; top: 125px;
    width: 228px; height: 3px; border-radius: 2px; background: var(--black);
  }
  .contact-row { position: absolute; left: 0; height: 18px; width: 360px; }
  .contact-row .tab {
    position: absolute; left: 0; top: 1px; width: 38px; height: 16px; background: var(--red);
  }
  .contact-row .icon { left: 20px; top: 0; width: 18px; height: 18px; border: 1px solid var(--red); }
  .contact-row .text {
    position: absolute; left: 39px; top: 0;
    color: var(--red); font-size: 14px; line-height: 18px; word-spacing: 3px;
    white-space: nowrap;
  }

  /* back */
  .services { position: absolute; left: 0; top: 0; list-style: none; }
  .services li, .slot {
    position: absolute; color: var(--white); font-size: 14px; line-height: 18px;
    white-space: nowrap; word-spacing: 3px;
  }
  .services li::before, .slot::before {
    content: ""; position: absolute; left: -11px; top: 5px;
    width: 8px; height: 8px; border-radius: 50%; background: var(--red);
  }
  .slot { top: 283px; }
  .slot--date { left: 37px; }
  .slot--time { left: 300px; }
  .write-line { position: absolute; top: 297px; height: 3px; background: var(--white); }
  .write-line--date { left: 75px; width: 182px; }
  .write-line--time { left: 339px; width: 182px; }
</style>
</head>
<body>

<section class="card card--front" aria-label="Card front">
  <div class="name-tab"></div>
  <div class="icon name-icon">
    <svg width="12" height="15" viewBox="0 0 12 15"><circle cx="6" cy="3" r="2.6"/><rect x="2.5" y="6.5" width="7" height="8.5" rx="1.5"/></svg>
  </div>
  <h1 class="name">Marlo Fenwicke</h1>
  <p class="role">(Managing director)</p>
  <div class="name-rule"></div>

  <div class="contact-row" style="top:169px">
    <span class="tab"></span>
    <span class="icon"><svg width="10" height="10" viewBox="0 0 10 10"><path d="M2 0.5l2 2-1 1.3c.7 1.4 1.8 2.5 3.2 3.2l1.3-1 2 2-1.4 1.5C4.8 9.2.8 5.2.5 1.9z"/></svg></span>
    <span class="text">027 451 9362</span>
  </div>
  <div class="contact-row" style="top:195px">
    <span class="tab"></span>
    <span class="icon"><svg width="12" height="10" viewBox="0 0 12 10"><path d="M1 3.5C1 1.5 11 1.5 11 3.5L9 4.5 8 3H4L3 4.5z"/><rect x="2.5" y="5" width="7" height="4.5" rx="1"/></svg></span>
    <span class="text">07 594 2713</span>
  </div>
  <div class="contact-row" style="top:219px">
    <span class="tab"></span>
    <span class="icon"><svg width="10" height="8" viewBox="0 0 10 8"><rect width="10" height="8" rx="1"/><path d="M0.5 1l4.5 3.5L9.5 1" stroke="#0c0c0c" stroke-width="1" fill="none"/></svg></span>
    <span class="text">office@keelstoneautomotive.example.nz</span>
  </div>
  <div class="contact-row" style="top:242px">
    <span class="tab"></span>
    <span class="icon"><svg width="12" height="12" viewBox="0 0 12 12" fill="none" stroke="#fff" stroke-width="1"><circle cx="6" cy="6" r="5"/><ellipse cx="6" cy="6" rx="2.2" ry="5"/><path d="M1 6h10"/></svg></span>
    <span class="text">keelstoneautomotive.example.nz</span>
  </div>
  <div class="contact-row" style="top:267px">
    <span class="tab"></span>
    <span class="icon"><svg width="11" height="10" viewBox="0 0 11 10"><path d="M5.5 0L11 5H9.5v5h-3V7h-2v3h-3V5H0z"/></svg></span>
    <span class="text">48 Tarn Lane Harrowby 3682</span>
  </div>

  <p class="wordmark">Keelstone Prime<br>Automotive</p>
</section>

<section class="card card--back" aria-label="Card back">
  <ul class="services">
    <li style="left:37px;top:125px">Vehicle Servicing</li>
    <li style="left:37px;top:150px">All Mechanical Repairs</li>
    <li style="left:36px;top:170px">Warrant of Fitness</li>
    <li style="left:37px;top:193px">Tyres &amp; Wheel Alignments</li>
    <li style="left:38px;top:218px">Automotive Parts &amp; Supplies</li>
    <li style="left:38px;top:242px">Automotive Diagnostics</li>
  </ul>
  <p class="slot slot--date">Date</p>
  <div class="write-line write-line--date"></div>
  <p class="slot slot--time">Time</p>
  <div class="write-line write-line--time"></div>

  <p class="wordmark">Keelstone Prime<br>Automotive</p>
</section>

</body>
</html>
```